Modern Verdell Tree Care Website

I need a website for a full service Tree Care company. The company provides tree pruning, tree removal, tree preservation, emergency services, stump grinding, and emergency tree services.

Target Market(s)

Customers that need tree services

Industry/Entity Type

Landscaping, Tree Services

Coding

Coded - Design and coding required

Number of Pages Required

5+ page

Font styles to use
Sans Serif

Requirements
Must have
• Good clean design that showcases the services the company provides.
Nice to have
• Services page; contact form, blog, home page, about page

```html
<!DOCTYPE html>
<html lang="en">
<head>
<meta charset="utf-8">
<title>Verdell Tree Care</title>
<link rel="stylesheet" href="https://fonts.googleapis.com/css2?family=Audiowide&family=Montserrat:wght@400;500;600;700;800&display=swap">
<style>
:root{
  --green:#8dc63f;
  --orange:#f9a83a;
  --slate:#5e6e78;
  --footer:#66757d;
  --cream:#fbf8ef;
  --ink:#333d42;
  --white:#ffffff;
}
*{box-sizing:border-box;margin:0;padding:0}
html,body{width:1200px;height:3340px;overflow:hidden}
body{position:relative;background:var(--cream);font-family:'Montserrat',sans-serif;color:var(--ink)}
.abs{position:absolute}
.display{font-family:'Audiowide',sans-serif;text-transform:uppercase;letter-spacing:1px}
.pill{position:absolute;border-radius:30px;background:var(--orange);color:#fff;font-weight:700;font-size:15px;display:flex;align-items:center;justify-content:center;text-transform:uppercase}
.photo{position:absolute}

/* header */
.topbar{left:0;top:0;width:1200px;height:6px;background:var(--green);border-radius:0 0 6px 6px}
.header{left:0;top:6px;width:1200px;height:100px;background:#fff}
.brand{left:145px;top:34px;display:flex;align-items:center;gap:12px}
.brand-mark{width:46px;height:46px;background:var(--green)}
.brand-name{font-weight:700;font-size:30px;color:var(--slate);letter-spacing:1px;line-height:1}
.callout{left:824px;top:22px;display:flex;gap:12px;align-items:center}
.callout small{display:block;font-size:16px;color:var(--ink)}
.callout strong{display:block;font-size:19px;font-weight:700;color:var(--ink)}
.nav{left:548px;top:72px;display:flex;gap:37px;font-size:15px;color:var(--ink);align-items:center}
.nav .home{display:flex;align-items:center;gap:6px}
.nav .home i{width:12px;height:12px;background:var(--green);display:inline-block}
.search{left:1029px;top:69px;width:24px;height:24px;border-radius:50%;background:var(--green)}

/* hero */
.hero{left:0;top:106px;width:1200px;height:502px;border-radius:210px 210px 0 0;background:linear-gradient(160deg,#3f4a22 0%,#6e7d2c 40%,#8a9a34 60%,#3e3520 100%)}
.hero h1{position:absolute;left:0;width:1200px;top:146px;text-align:center;color:#fff;font-size:56px;line-height:64px;font-weight:400}
.hero .pill{left:523px;top:311px;width:155px;height:56px}
.dots{left:1110px;top:418px;display:flex;flex-direction:column;gap:10px}
.dots span{width:6px;height:6px;border-radius:50%;background:#fff}
.dots span:nth-child(2){background:var(--orange)}

/* about */
.about-photo{left:144px;top:683px;width:373px;height:373px;background:linear-gradient(180deg,#8c9a5e 0%,#5f6b37 55%,#4a3826 100%)}
.about h2{position:absolute;left:574px;top:686px;font-size:50px;color:var(--slate);font-weight:400}
.about p{position:absolute;left:575px;top:761px;width:482px;font-size:14.5px;line-height:25.3px;text-align:justify;color:#444}
.about .pill{left:575px;top:989px;width:153px;height:56px}
.tree-art{left:881px;top:985px;width:292px;height:181px;background:radial-gradient(ellipse at 50% 40%,#5d8a2f 0%,#7ea54a 45%,#fbf8ef 72%)}

/* why */
.why-left{left:0;top:1182px;width:360px;height:524px;background:linear-gradient(135deg,#7a5a36,#b07a46 50%,#6d5234)}
.why-right{left:840px;top:1182px;width:360px;height:524px;background:linear-gradient(135deg,#8b6b42,#c48a52 50%,#6a5134)}
.why-panel{left:348px;top:1078px;width:504px;height:640px}
.why h2{position:absolute;left:350px;width:500px;top:1238px;text-align:center;color:#fff;font-size:50px;line-height:64px;font-weight:400}
.why ul{position:absolute;left:466px;top:1390px;list-style:none}
.why li{font-size:18.5px;line-height:35px;color:#fff6dc;position:relative;padding-left:28px}
.why li::before{content:"";position:absolute;left:0;top:14px;width:9px;height:9px;border-radius:50%;background:#fff}
.saw-a{left:580px;top:1650px;width:255px;height:48px;background:#c6e39a;border-radius:4px}

/* services */
.services-bg{left:0;top:1706px;width:1200px;height:930px;background:var(--cream)}
.services h2{position:absolute;left:0;width:1200px;top:1782px;text-align:center;font-size:52px;color:var(--slate);font-weight:400}
.card{position:absolute;width:293px;height:272px;background:#fff;overflow:hidden}
.card .img{position:absolute;left:0;top:0;width:293px;height:240px}
.card svg{position:absolute;left:0;top:180px}
.card span{position:absolute;left:0;bottom:0;width:293px;height:46px;text-align:center;font-size:19px;font-weight:500;color:var(--ink);line-height:34px;text-transform:uppercase}
.services .pill{left:482px;top:2493px;width:236px;height:56px;font-size:15px}

/* cta */
.cta{left:0;top:2618px;width:1200px;height:262px;background:var(--green);border-radius:250px 250px 0 0}
.saw-b{left:640px;top:2560px;width:495px;height:118px;background:#eef3e6;border-radius:6px}
.cta h3{position:absolute;left:174px;top:2678px;color:#fff;font-size:32px;line-height:40px;font-weight:400}
.cta .phone-ring{left:727px;top:2719px;width:52px;height:52px;border:3px solid #fff;border-radius:50%;display:flex;align-items:center;justify-content:center}
.cta .numbers{left:789px;top:2712px;color:#fff;font-size:35px;line-height:44px;font-weight:500}

/* footer */
.footer{left:0;top:2880px;width:1200px;height:460px;background:var(--footer);color:#fff}
.footer h4{position:absolute;top:2942px;font-size:20px;font-weight:800}
.info-row{position:absolute;left:155px;display:flex;align-items:center;gap:14px}
.ico{width:34px;height:34px;border-radius:50%;border:2px solid #fff;display:flex;align-items:center;justify-content:center;flex:none}
.ico.fill{background:var(--green);border-color:var(--green)}
.info-row .sm{font-size:13px;line-height:22px}
.info-row .lg{font-size:17px;font-weight:500}
.social{left:157px;top:3158px;display:flex;gap:6px}
.social span{width:27px;height:27px;border-radius:50%;background:#2d4fa0}
.social span:nth-child(2){background:#d63a3a}
.social span:nth-child(3){background:#a8884e}
.field{position:absolute;background:#fff;border:1px solid #d6dadc;font-size:11px;color:#777;padding:8px 10px}
.submit{left:927px;top:3186px;width:118px;height:28px;border-radius:14px;background:var(--green);color:#fff;font-family:Georgia,serif;font-size:13px;font-weight:700;display:flex;align-items:center;justify-content:center}
.rule{left:123px;top:3256px;width:933px;height:1px;background:#8a979d}
.copy{left:0;width:1200px;top:3292px;text-align:center;font-size:13px}
</style>
</head>
<body>

<div class="abs topbar"></div>
<header class="abs header"></header>
<div class="abs brand"><span class="brand-mark"></span><span class="brand-name">VERDELL TREE CARE</span></div>
<div class="abs callout">
  <svg width="32" height="32" viewBox="0 0 32 32"><circle cx="16" cy="16" r="14" fill="none" stroke="#f9a83a" stroke-width="2.5"/><path d="M11 9c1 0 2 2 3 4l-2 2c1 2 3 4 5 5l2-2c2 1 4 2 4 3 0 2-2 3-4 3C13 24 8 19 8 13c0-2 1-4 3-4z" fill="#f9a83a"/></svg>
  <div><small>Call for a free estimate</small><strong>(555) 214-7730</strong></div>
</div>
<nav class="abs nav"><span class="home"><i></i>HOME</span><span>ABOUT</span><span>SERVICES</span><span>CONTACT</span><span>BLOG</span></nav>
<div class="abs search"><svg width="24" height="24" viewBox="0 0 24 24"><circle cx="11" cy="11" r="4" fill="none" stroke="#fff" stroke-width="2"/><path d="M14 14l3 3" stroke="#fff" stroke-width="2"/></svg></div>

<section class="abs hero" role="img" aria-label="Arborist climbing a large tree in a green forest">
  <h1 class="display">Serving Lafayette and<br>surrounding areas</h1>
  <div class="pill">Get Started</div>
</section>
<div class="abs dots"><span></span><span></span><span></span></div>

<section class="about">
  <div class="photo about-photo" role="img" aria-label="Workers planting a young tree seedling in soil"></div>
  <h2 class="display">About Us</h2>
  <p>At Verdell Tree Care, we are more than just a tree service company, we are stewards of our beautiful trees. With a passion deeply rooted in arboriculture, we embark on a mission to promote the health, beauty, and safety of your trees and landscapes.<br>Whether it's expert tree trimming to enhance aesthetics, meticulous tree removal to mitigate hazards, or comprehensive tree health assessments to ensure safety, we approach each task with unwavering dedication and attention to detail.</p>
  <div class="pill">Read More</div>
  <div class="photo tree-art" role="img" aria-label="Illustration of a broad green oak tree"></div>
</section>

<section class="why">
  <div class="photo why-left" role="img" aria-label="Compact loader working in a wooded yard"></div>
  <div class="photo why-right" role="img" aria-label="Worker in hard hat walking among trees"></div>
  <svg class="abs why-panel" viewBox="0 0 504 640" width="504" height="640">
    <path d="M2 130 Q2 114 16 108 L236 6 Q252 -1 268 6 L488 108 Q502 114 502 130 L502 640 L2 640 Z" fill="#fff"/>
    <path d="M14 134 Q14 122 26 117 L240 19 Q252 14 264 19 L478 117 Q490 122 490 134 L490 640 L14 640 Z" fill="#8dc63f"/>
  </svg>
  <h2 class="display">Why<br>choose us</h2>
  <ul>
    <li>Licensed and Insured</li>
    <li>24-Hours Emergency Services</li>
    <li>Locally Owned &amp; Operated</li>
    <li>Professional Work</li>
    <li>Safety is Our NO Priority</li>
    <li>Free Estimates</li>
    <li>Licensed Arborist on Staff</li>
  </ul>
  <div class="abs saw-a" role="img" aria-label="Chainsaw silhouette"></div>
</section>

<section class="services">
  <div class="abs services-bg"></div>
  <h2 class="display">Our Services</h2>

  <div class="card" style="left:144px;top:1880px"><div class="img" role="img" aria-label="Arborist trimming branches with loppers" style="background:linear-gradient(160deg,#3f6e2a,#86b04e)"></div><svg width="293" height="92" viewBox="0 0 293 92"><path d="M0 92 L0 40 Q146 0 293 40 L293 92 Z" fill="#fff"/></svg><span>Tree Trimming</span></div>
  <div class="card" style="left:454px;top:1880px"><div class="img" role="img" aria-label="Climber cutting a large trunk against blue sky" style="background:linear-gradient(160deg,#4a7dc8,#7a6a4a)"></div><svg width="293" height="92" viewBox="0 0 293 92"><path d="M0 92 L0 40 Q146 0 293 40 L293 92 Z" fill="#fff"/></svg><span>Tree Removal</span></div>
  <div class="card" style="left:763px;top:1880px"><div class="img" role="img" aria-label="Crew cleaning up a city park planting bed" style="background:linear-gradient(160deg,#7f8a6a,#b4923e 60%,#4b4a3a)"></div><svg width="293" height="92" viewBox="0 0 293 92"><path d="M0 92 L0 40 Q146 0 293 40 L293 92 Z" fill="#fff"/></svg><span>Tree Cleaning</span></div>

  <div class="card" style="left:144px;top:2168px"><div class="img" role="img" aria-label="Gloved hand sawing a branch" style="background:linear-gradient(160deg,#6b6a58,#c96b36 55%,#5a5446)"></div><svg width="293" height="92" viewBox="0 0 293 92"><path d="M0 92 L0 40 Q146 0 293 40 L293 92 Z" fill="#fff"/></svg><span>Tree Pruning</span></div>
  <div class="card" style="left:454px;top:2168px"><div class="img" role="img" aria-label="Worker grinding a tree stump" style="background:linear-gradient(160deg,#d66a2a,#8a5a36 55%,#3e3a34)"></div><svg width="293" height="92" viewBox="0 0 293 92"><path d="M0 92 L0 40 Q146 0 293 40 L293 92 Z" fill="#fff"/></svg><span>Stump Grinding</span></div>
  <div class="card" style="left:763px;top:2168px"><div class="img" role="img" aria-label="People planting saplings in a forest" style="background:linear-gradient(160deg,#6e7a46,#4a3a2c 65%,#2e2a24)"></div><svg width="293" height="92" viewBox="0 0 293 92"><path d="M0 92 L0 40 Q146 0 293 40 L293 92 Z" fill="#fff"/></svg><span>Tree Preservation</span></div>

  <div class="pill">View More Services</div>
</section>

<section class="cta">
  <div class="abs cta"></div>
  <div class="abs saw-b" role="img" aria-label="Chainsaw illustration"></div>
  <h3 class="display">Call us today to<br>see how we can help<br>you with all of your<br>tree needs</h3>
  <div class="abs phone-ring"><svg width="28" height="28" viewBox="0 0 32 32"><path d="M9 5c2 0 3 3 4 5l-3 3c2 4 5 7 9 9l3-3c2 1 5 2 5 4 0 3-3 5-6 5C12 28 4 20 4 11c0-3 2-6 5-6z" fill="none" stroke="#fff" stroke-width="2.2"/></svg></div>
  <div class="abs numbers">(555) 214-7730<br>(555) 380-4162</div>
</section>

<footer>
  <div class="abs footer"></div>
  <h4 style="left:155px">Contact Info</h4>
  <div class="info-row" style="top:2995px"><span class="ico"><svg width="14" height="16" viewBox="0 0 14 16"><path d="M7 1a5 5 0 0 1 5 5c0 4-5 9-5 9S2 10 2 6a5 5 0 0 1 5-5z" fill="none" stroke="#fff" stroke-width="1.6"/><circle cx="7" cy="6" r="1.6" fill="#fff"/></svg></span><span class="sm">233,Sed ut perspiciatis unde<br>omnis iste natus error sit voluptatem</span></div>
  <div class="info-row" style="top:3048px"><span class="ico fill"><svg width="16" height="16" viewBox="0 0 32 32"><path d="M9 5c2 0 3 3 4 5l-3 3c2 4 5 7 9 9l3-3c2 1 5 2 5 4 0 3-3 5-6 5C12 28 4 20 4 11c0-3 2-6 5-6z" fill="#fff"/></svg></span><span class="lg">(555) 214-7730 (555) 380-4162</span></div>
  <div class="info-row" style="top:3100px"><span class="ico"><svg width="16" height="12" viewBox="0 0 16 12"><rect x="1" y="1" width="14" height="10" fill="#fff"/><path d="M1 1l7 6 7-6" fill="none" stroke="#66757d" stroke-width="1.4"/></svg></span><span class="sm">E-Mail: info@verdelltreecare.com</span></div>
  <div class="abs social"><span></span><span></span><span></span></div>

  <h4 style="left:499px">Get In Touch</h4>
  <div class="field" style="left:501px;top:2987px;width:266px;height:29px">Enter NAme</div>
  <div class="field" style="left:778px;top:2987px;width:267px;height:29px">Enter Email</div>
  <div class="field" style="left:501px;top:3027px;width:266px;height:29px">Phone</div>
  <div class="field" style="left:778px;top:3027px;width:267px;height:29px">Zipcode</div>
  <div class="field" style="left:501px;top:3067px;width:544px;height:29px">Address</div>
  <div class="field" style="left:501px;top:3106px;width:544px;height:66px">Message</div>
  <div class="abs submit">SUBMIT</div>

  <div class="abs rule"></div>
  <div class="abs copy">copyright © 2024 Verdell Tree Care.All rights reserved &nbsp;|&nbsp; Privacy Policy</div>
</footer>

</body>
</html>
```